Copperleaf Balustrade Website Redesign

I want a fresh new design for my website. Original website
www.copperleafbalustrade-example.com. Will need to add additional photos for winning designer. Please use the basic layout for new design. Looking to get a more modern, functional site to attract new customer and ne bale to highlight past projects. Need it to be easy to navigate and get in touch with me for inquiries.

Target Market(s)

Builders and home owners in WA state

Industry/Entity Type

Building, Construction, Deck building

Coding

Coded - Design and coding required

Number of Pages Required

5+ page

Font styles to use
Sans Serif

Colors
0054AA
0677BA
7BADD7
CADEEF
E8F1F8
0094D4
00A9DD
6FCCEA
C7EBF8
E9F6FB
00AB8E
00BBA5
67D7C9
C6EFE9
E9F9F6
59FF00
82FF00
B8FF75
E3FFCB
F4FFEA

Requirements
Must have
• Will need to add more photos of completed projects
Nice to have
• Fresh take on old website, something modern
Should not have
• Nothing comes to mind

```html
<!DOCTYPE html>
<html lang="en">
<head>
<meta charset="utf-8">
<title>Copperleaf Balustrade</title>
<link rel="stylesheet" href="https://fonts.googleapis.com/css2?family=Roboto:wght@400;500;700&family=Lora:ital@1&display=swap">
<style>
:root{
  --green:#17704a;
  --green-dark:#0f5a39;
  --teal:#1aa27f;
  --mint:#4fd1bf;
  --lime:#b8ff75;
  --sky:#e3eff8;
  --sky-deep:#c7e5f5;
  --card:#dde9f4;
  --ink:#222;
  --muted:#3a3a3a;
  --navy:#1d4fa0;
}
*{box-sizing:border-box;margin:0;padding:0}
html,body{width:1200px;height:4946px;overflow:hidden}
body{position:relative;background:#fff;font-family:'Roboto',sans-serif;color:var(--ink)}
.abs{position:absolute}
.serif{font-family:'Lora',serif;font-style:italic;font-weight:400}
.accent{color:var(--teal)}
.photo{position:absolute}

.topbar{left:0;top:0;width:1200px;height:82px;background:var(--sky)}
.topbar .meta{position:absolute;top:24px;font-size:12px;color:#333}
.nav{left:138px;top:62px;width:924px;height:50px;background:var(--green);display:flex;justify-content:space-between;align-items:center;padding:0 48px 0 56px;border-bottom:3px solid var(--mint)}
.nav ul{list-style:none;display:flex;gap:28px;font-size:13px;color:#fff}
.nav li.active{color:var(--lime);font-weight:700}
.nav ul.right{gap:32px}
.badge{left:509px;top:0;width:178px;height:188px;background:#fff;clip-path:polygon(0 0,100% 0,100% 78%,50% 100%,0 78%);display:flex;flex-direction:column;align-items:center;justify-content:center;padding-bottom:30px;z-index:3}
.badge span{font-size:22px;font-weight:500;color:var(--green);line-height:1.25;text-align:center}

.hero-photo{left:0;top:82px;width:1200px;height:560px;background:linear-gradient(160deg,#5d6b5c 0%,#3b4244 40%,#24292c 70%,#4a4f52 100%)}
.hero-curve{left:0;top:560px;width:1200px;height:150px}
.welcome{left:138px;top:470px;width:440px;height:100px;background:rgba(40,40,40,.55);padding:16px 16px}
.welcome .serif{font-size:28px;color:#fff;line-height:1}
.welcome h1{font-size:36px;font-weight:700;color:#fff;margin-top:6px;white-space:nowrap}
.contact-card{left:791px;top:142px;width:271px;height:411px;background:#fff;border:3px solid var(--sky-deep)}
.contact-card .head{background:var(--teal);height:85px;text-align:center;color:#fff;padding-top:18px}
.contact-card .head h2{font-size:26px;font-weight:500}
.contact-card .head p{font-family:'Lora',serif;font-size:17px}
.field{margin:0 20px;height:32px;border:1px solid #c9d6e0;font-size:10px;color:#888;padding:9px 14px;margin-top:9px}
.field.tall{height:94px}
.btn{background:var(--green-dark);color:#fff;font-weight:700;text-align:center}
.contact-card .btn{margin:13px 20px 0;height:40px;line-height:40px;font-size:18px}

.eyebrow{font-size:30px;color:#555}
.title{font-size:38px;font-weight:700;color:var(--green-dark)}
.rule{width:90px;height:2px;background:var(--mint);margin-top:6px}
.body-text{font-size:13px;line-height:19px;color:var(--muted)}
.about-photo{left:600px;top:743px;width:462px;height:371px;clip-path:polygon(10% 0,100% 0,100% 100%,0 100%,0 12%)}
.about-photo .fill{position:absolute;left:12px;top:12px;right:0;bottom:0;background:linear-gradient(180deg,#bfc4ba,#8f8a6c 55%,#3d4a3c);clip-path:polygon(10% 0,100% 0,100% 100%,0 100%,0 12%)}

.products-bg{left:0;top:1200px;width:1200px;height:540px;background:var(--sky);clip-path:polygon(0 0,100% 0,100% 88%,50% 100%,0 88%)}
.prod-photo{left:138px;top:1290px;width:447px;height:348px;background:var(--mint);clip-path:polygon(8% 0,100% 0,100% 90%,90% 100%,0 100%,0 12%)}
.prod-photo .fill{position:absolute;left:12px;top:12px;right:12px;bottom:0;background:linear-gradient(135deg,#cfd3d2,#7b7f80 50%,#5a5e5f);clip-path:polygon(8% 0,100% 0,100% 90%,90% 100%,0 100%,0 12%)}
.prod-list{list-style:none}
.prod-list li{font-size:18px;font-weight:500;position:relative;padding-left:20px;color:#1f2a2a}
.prod-list li::before{content:"";position:absolute;left:6px;top:8px;width:8px;height:8px;border-radius:50%;background:var(--teal)}
.prod-active{left:610px;top:1415px;width:452px;height:115px;background:#bde3f3;padding:10px 18px 0 14px}
.prod-active h3{font-size:18px;font-weight:500;color:var(--green);position:relative;padding-left:20px}
.prod-active h3::before{content:"";position:absolute;left:6px;top:7px;width:8px;height:8px;border-radius:50%;background:var(--teal)}
.prod-active p{font-size:12px;line-height:19px;color:#333;margin-top:10px;padding-left:20px}

.card{background:var(--card);padding:0 14px}
.card .img{height:161px;margin:0 0 16px}
.card h4{font-size:16px;font-weight:700;line-height:20px;color:#1f1f1f;margin-bottom:8px}
.card p{font-size:12px;line-height:19px;color:#3d3d3d}

.step{border-radius:50%;background:var(--teal);border:6px solid #fff;box-shadow:0 0 0 1px #cfe2ee;color:#fff;font-size:60px;font-weight:700;display:flex;align-items:center;justify-content:center}
.step-text{text-align:center}
.step-text h5{font-size:15px;font-weight:700;margin-bottom:10px}
.step-text p{font-size:12px;line-height:19px;color:#3b3b3b}

.h2c{text-align:center;font-size:36px;font-weight:700;color:var(--green-dark)}
.proj{border:3px solid var(--teal)}
.proj .fill{position:absolute;inset:6px}
.dots span{display:inline-block;width:13px;height:13px;background:var(--teal);margin:0 6px}
.dots span.off{background:#b6c4ce}

.serving-bg{left:0;top:3696px;width:1200px;height:560px;background:var(--sky)}
.map-area{left:177px;top:3869px;width:393px;height:259px;background:linear-gradient(135deg,#2a5db0,#1d4fa0 60%,#173f85)}
.contact-dark{left:0;top:4176px;width:1200px;height:438px;background:linear-gradient(180deg,#2c3436,#1c2124 60%,#2a2e2f)}
.contact-point{left:0;top:4175px;width:1200px;height:80px}
.tagline{left:292px;top:4512px;width:610px;height:42px;border:1px dashed var(--teal);text-align:center;line-height:40px;font-size:16px;color:#fff}

.foot-head{font-size:26px;font-weight:500;color:var(--green-dark)}
.foot-field{border:1px solid #c9d6e0;height:33px;font-size:10px;color:#777;padding:10px 8px}
.footer-bar{left:0;top:4886px;width:1200px;height:60px;background:var(--green-dark);color:#fff;font-size:13px}
.social{width:20px;height:20px;border-radius:50%;border:2px solid #fff;top:20px}
</style>
</head>
<body>

<div class="abs topbar">
  <span class="meta" style="left:280px">LICENSED, INSURED, &amp; BONDED</span>
  <span class="meta" style="left:728px">WA GC LICENSE # COPPEBL911QA &nbsp;|&nbsp; Formed in 2020</span>
</div>
<div class="abs hero-photo photo" role="img" aria-label="Photo of a modern deck with glass and aluminum railings"></div>
<nav class="abs nav">
  <ul><li class="active">Home</li><li>Products</li><li>About</li><li>Overview</li></ul>
  <ul class="right"><li>Railing Projects</li><li>Remodel Projects</li><li>Contact</li></ul>
</nav>
<div class="abs badge"><span>Copperleaf<br>Balustrade</span></div>

<div class="abs welcome">
  <div class="serif">Welcome</div>
  <h1>Copperleaf Balustrade</h1>
</div>

<form class="abs contact-card">
  <div class="head"><h2>Get in touch</h2><p>with me for inquiries.</p></div>
  <div class="field">Enter Your Name</div>
  <div class="field">Enter Your email</div>
  <div class="field">Enter Your Phone number</div>
  <div class="field tall">Enter Your Message</div>
  <div class="btn">Submit</div>
</form>

<svg class="abs hero-curve" viewBox="0 0 1200 150" preserveAspectRatio="none">
  <path d="M0 20 Q600 150 1200 20 L1200 150 L0 150Z" fill="#dcebf6"/>
  <path d="M0 55 Q600 160 1200 55 L1200 150 L0 150Z" fill="#ffffff"/>
</svg>

<div class="abs" style="left:142px;top:758px;width:440px">
  <div class="serif eyebrow">About Us</div>
  <div class="title" style="font-size:36px">Copperleaf <span class="accent">Balustrade</span></div>
  <div class="rule"></div>
  <p class="body-text" style="margin-top:22px">At Copperleaf Balustrade, we believe that every outdoor space deserves the perfect blend of style, safety, and durability. Serving homeowners, builders, and commercial developers across the Washington State, we specialize in crafting custom railing systems designed to withstand the region's unique climate while enhancing the beauty of your outdoor living spaces.</p>
  <p class="body-text" style="margin-top:19px">With a focus on premium materials, expert craftsmanship, and exceptional customer service, Copperleaf Balustrade is proud to be the trusted partner for both residential and commercial railing projects. Whether you're looking to complement a new deck, add a modern touch to your balcony, or create a secure and stunning barrier for a commercial space, we've got the perfect solution for you.</p>
</div>
<div class="abs about-photo" style="background:var(--mint)">
  <div class="fill" role="img" aria-label="Photo of a multi-storey building with black balcony railings"></div>
</div>

<div class="abs products-bg"></div>
<div class="abs prod-photo"><div class="fill" role="img" aria-label="Photo of black aluminum stair railing beside a grey wall"></div></div>
<div class="abs" style="left:610px;top:1255px;width:452px">
  <div class="serif eyebrow" style="font-size:28px">Products</div>
  <div class="title" style="font-size:36px">Our <span class="accent">Products</span></div>
  <div class="rule"></div>
  <p class="body-text" style="margin-top:20px">We offer a wide variety of custom and railing systems designed to meet the needs of every project:</p>
</div>
<div class="abs prod-active">
  <h3>Aluminum Railings</h3>
  <p>For a sleek, low-maintenance option, our powder-coated aluminum railings provide strength, corrosion resistance, and a modern aesthetic. Available in a range of colors and finishes.</p>
</div>
<ul class="abs prod-list" style="left:614px;top:1548px">
  <li style="margin-bottom:25px">Glass Railings</li>
  <li style="margin-bottom:22px">Cable Railings</li>
  <li>Custom</li>
</ul>

<div class="abs" style="left:136px;top:1845px">
  <div class="serif eyebrow" style="font-size:28px">Overview</div>
  <div class="title" style="font-size:36px">Why Choose <span class="accent">Copperleaf Balustrade ?</span></div>
  <div class="rule"></div>
</div>

<div class="abs card" style="left:138px;top:1974px;width:208px;height:413px">
  <div class="img" role="img" aria-label="Photo of a worker measuring a railing component" style="background:linear-gradient(135deg,#c7c9cc,#3c5fa8 60%,#a08a6a)"></div>
  <h4>Locally Crafted, Regionally Resilient:</h4>
  <p>Our railings are designed with the Pacific Northwest's weather in mind—rain, snow, and everything in between. We use durable materials that are resistant to corrosion, moisture, and the elements, ensuring your railings stand the test of time.</p>
</div>
<div class="abs card" style="left:376px;top:2035px;width:210px;height:400px">
  <div class="img" role="img" aria-label="Photo of an installer fitting a stainless railing post" style="background:linear-gradient(135deg,#b9a78b,#d8dadc 50%,#6d7378)"></div>
  <h4>Custom Solutions for Every Need:</h4>
  <p>We work closely with you to design and fabricate custom railing systems that perfectly suit your space, style, and functional requirements. From intricate designs to minimalistic finishes, we tailor every project to your vision.</p>
</div>
<div class="abs card" style="left:612px;top:1974px;width:212px;height:413px">
  <div class="img" role="img" aria-label="Photo of cable railing mounted on a wooden deck" style="background:linear-gradient(135deg,#a0714a,#d4a77a 50%,#5a3b25)"></div>
  <h4>Expert Installation &amp; Craftsmanship:</h4>
  <p>Our skilled craftsmen take pride in delivering exceptional workmanship, while our professional installers ensure every railing is securely mounted and aligned to meet local safety codes.</p>
</div>
<div class="abs card" style="left:851px;top:2035px;width:211px;height:400px">
  <div class="img" role="img" aria-label="Photo of installers working on a deck railing at sunset" style="background:linear-gradient(160deg,#9db3c4,#6b5a48 60%,#2f2a25)"></div>
  <h4 style="margin-bottom:28px">Full-Service Partner:</h4>
  <p>From the initial consultation and design process to installation and ongoing maintenance, we are with you every step of the way to ensure your project exceeds expectations.</p>
</div>

<svg class="abs" style="left:0;top:2538px" width="1200" height="540" viewBox="0 0 1200 540">
  <path d="M0 0 H1200 V470 Q600 560 0 470Z" fill="#e3eff8"/>
</svg>
<div class="abs h2c" style="left:0;top:2596px;width:1200px">Our <span class="accent">Process</span></div>
<svg class="abs" style="left:0;top:2700px" width="1200" height="300" viewBox="0 0 1200 300">
  <path d="M400 105 C470 110 460 180 520 195" fill="none" stroke="#1aa27f" stroke-width="2" stroke-dasharray="6 5"/>
  <path d="M688 195 C740 180 720 110 795 105" fill="none" stroke="#1aa27f" stroke-width="2" stroke-dasharray="6 5"/>
</svg>
<div class="abs step" style="left:238px;top:2688px;width:166px;height:166px">01</div>
<div class="abs step" style="left:516px;top:2841px;width:166px;height:166px">02</div>
<div class="abs step" style="left:794px;top:2688px;width:166px;height:166px">03</div>
<div class="abs step-text" style="left:480px;top:2693px;width:240px">
  <h5>Professional Installation</h5>
  <p>Our experienced team handles all aspects of installation, from measuring to securing, ensuring your railing is safe, secure, and perfectly aligned.</p>
</div>
<div class="abs step-text" style="left:200px;top:2882px;width:242px">
  <h5>Consultation &amp; Design</h5>
  <p>We start by listening to your vision and understanding your specific needs. Our team will offer expert advice and design ideas to help you choose the best materials and styles.</p>
</div>
<div class="abs step-text" style="left:756px;top:2887px;width:244px">
  <h5>Ongoing Support</h5>
  <p>We offer warranties on all of our products and services, and we are always available to help with maintenance or modifications down the road.</p>
</div>

<div class="abs h2c" style="left:0;top:3184px;width:1200px">Our <span class="accent">Past Projects</span></div>
<div class="abs" style="left:0;top:3293px;width:90px;height:8px;background:var(--teal)"></div>
<div class="abs proj" style="left:-4px;top:3295px;width:369px;height:244px;border-color:#cfe2ee">
  <div class="fill" role="img" aria-label="Photo of a deck with cable railing overlooking a valley" style="background:linear-gradient(180deg,#b4c5d4,#6f7d6c 50%,#5b5d5f)"></div>
</div>
<div class="abs" style="left:357px;top:3380px;width:8px;height:159px;background:var(--teal)"></div>
<div class="abs proj" style="left:378px;top:3264px;width:444px;height:303px">
  <div class="fill" role="img" aria-label="Photo of a patio with black metal railing and outdoor furniture" style="background:linear-gradient(180deg,#6b8a4e,#2c3a2e 45%,#6f8aa8)"></div>
</div>
<div class="abs" style="left:833px;top:3293px;width:120px;height:8px;background:var(--teal)"></div>
<div class="abs proj" style="left:833px;top:3295px;width:371px;height:244px;border-color:#cfe2ee">
  <div class="fill" role="img" aria-label="Photo of a dark modern house with glass balcony railing" style="background:linear-gradient(180deg,#c9d4dc,#3e4346 45%,#2a2d2f)"></div>
</div>
<div class="abs" style="left:833px;top:3380px;width:8px;height:159px;background:var(--teal)"></div>
<div class="abs dots" style="left:0;top:3594px;width:1200px;text-align:center">
  <span></span><span></span><span class="off"></span><span></span><span></span>
</div>

<div class="abs serving-bg"></div>
<div class="abs h2c" style="left:0;top:3745px;width:1200px">Serving <span class="accent">Washington State</span></div>
<div class="abs rule" style="left:555px;top:3803px"></div>
<div class="abs map-area" role="img" aria-label="Map of Washington State with service location pins"></div>
<p class="abs" style="left:610px;top:3893px;width:364px;font-size:15px;line-height:24px;text-align:center;color:#222"><b>Copperleaf Balustrade</b> is proud to serve the entire state of Washington. Whether you're upgrading your home's deck or outfitting a commercial space, we understand the importance of creating beautiful, durable railings that stand up to the region's diverse and often challenging weather conditions.</p>

<div class="abs contact-dark" role="img" aria-label="Photo of a deck railing overlooking forested hills at dusk"></div>
<svg class="abs contact-point" viewBox="0 0 1200 80" preserveAspectRatio="none">
  <path d="M0 0 H1200 L600 80Z" fill="#e3eff8"/>
</svg>
<div class="abs" style="left:0;top:4330px;width:1200px;text-align:center;color:#fff">
  <div style="font-size:34px;font-weight:500">Contact Us</div>
  <p style="width:660px;margin:40px auto 0;font-size:19px;line-height:24px">Ready to elevate your space with a custom railing solution that's built to last? Reach out to the <b class="accent">Copperleaf Balustrade</b> team for a free consultation. Let us bring your vision to life with craftsmanship, care, and precision.</p>
</div>
<div class="abs tagline"><b class="accent">Copperleaf Balustrade</b> — Durable, stylish, and built for the Pacific Northwest.</div>

<div class="abs" style="left:140px;top:4660px;width:170px;text-align:center;font-size:26px;font-weight:500;color:var(--green);line-height:1.3">Copperleaf<br>Balustrade</div>

<div class="abs" style="left:405px;top:4660px;width:280px">
  <div class="foot-head">Contact Info</div>
  <div style="display:flex;gap:20px;margin-top:24px;font-size:14px;line-height:19px">
    <svg width="12" height="16" viewBox="0 0 12 16"><path d="M6 0C2.7 0 0 2.6 0 5.9 0 10 6 16 6 16s6-6 6-10.1C12 2.6 9.3 0 6 0zm0 8.2A2.3 2.3 0 1 1 6 3.6a2.3 2.3 0 0 1 0 4.6z" fill="#1aa27f"/></svg>
    <div>1450 Alder Crest Rd<br>Yakima, WA 98900<br>(206) 555-0148</div>
  </div>
  <div style="display:flex;gap:18px;margin-top:24px;align-items:center">
    <svg width="14" height="11" viewBox="0 0 14 11"><rect width="14" height="11" rx="1" fill="#1aa27f"/><path d="M1 1.5 7 6l6-4.5" fill="none" stroke="#fff" stroke-width="1.3"/></svg>
    <div style="font-size:12px;white-space:nowrap">info@copperleafbalustrade-example.com</div>
  </div>
</div>

<div class="abs" style="left:689px;top:4660px;width:373px">
  <div class="foot-head">Request a Quote</div>
  <div style="display:grid;grid-template-columns:1fr 1fr;gap:10px 10px;margin-top:16px">
    <div class="foot-field">Enter Your Name</div>
    <div class="foot-field">Enter Your Email</div>
    <div class="foot-field">Enter Phone Number</div>
    <div class="foot-field">Message</div>
  </div>
  <div class="btn" style="margin-top:17px;height:33px;line-height:33px;font-size:14px;font-weight:400">Submit</div>
</div>

<div class="abs footer-bar">
  <span class="abs" style="left:138px;top:21px">© 2024 &nbsp;|&nbsp; www.copperleafbalustrade-example.com</span>
  <span class="abs social" style="left:950px"></span>
  <span class="abs social" style="left:995px"></span>
  <span class="abs social" style="left:1041px"></span>
</div>

</body>
</html>
```